Medical centre needs a business card

We are a medcial centre in Australia, needing a new business card. Our demographic is low working class families. We are going to be renovating our premises to modernise the look and also had a new logo done a few months ago representing quality and community, and now need to update our cards. It needs to be doubled sided, with logo and contact details on the front, and appointment details on the back. . Needs to be modern and simple, easy to read. <br/><br/>Name: Kindle Grove Medical Centre <br/>Address: 512 Parmley Rd (Cnr Parmley Rd & Osgood Creek Rd),<br/>Tindarra Court Shopping Centre, Paralowie, SA 5108<br/>Ph: 08 8461 3072<br/>Tag line: Where your wellbeing comes first<br/>Website: www.kindlegrovemedicalcentre-example.com.au<br/>Online bookings also available<br/><br/>(On the back, to have 3 lines of appointments that can be written in.<br/>Day, date, time)<br/><br/>Your next appointment is on<br/>Can try “M T W Th F Sa Su _________________ at ____________ am/pm” or other combinations <br/>Please advise as soon as possible if unable to attend<br/>Cancellation fees apply if less than 2 hrs notice<br/>Online appointments available (please highlight this option by either by position, colour or font)

Target Market(s)

Lower social economic working class, young families to seniors

Industry/Entity Type

Medical Centre

Contact Information for Business Card

Kindle Grove Medical Centre
512 Parmley Rd (Cnr Parmley Rd & Osgood Creek Drive)
Tindarra Court Shopping Centre
Brenton Vale SA 5120
Ph: 08 8461 3072
www.kindlegrovemedicalcentre-example.com.au
Tagline line: where your wellbeing comes first
Back side is for appointments
Your next appointment is with Dr ______________
Day/date/time (Please give 3 lines of appointments)
Please advise as soon as possible if unable to attend
Cancellation fees apply if less than 2 hours notice
Online appointments available
Book online easily and conveniently (please highlight online appointments)

Font styles to use
Serif
Sans Serif

Colors

Designer to choose colors to be used in the design.

Requirements
Must have
• Modern and simple
• Easy to ready
• Induces a wellbeing feeling
• Incorporate our logo colours and feel from logo
• Induces feeling of stability and security
Nice to have
• Attract attention
• Pleasant to look at
• Feeling of innovation
Should not have
• Loud clashing colours
• Overly luxurious feeling
• Overly artistic

```html
<!DOCTYPE html>
<html lang="en">
<head>
<meta charset="utf-8">
<title>Kindle Grove Medical Centre – Business Card</title>
<link rel="stylesheet" href="https://fonts.googleapis.com/css2?family=Montserrat:wght@500;600;700&family=Roboto:wght@400;500;700&display=swap">
<style>
  :root {
    --brand-blue: #1779c9;
    --brand-green: #8cc63f;
    --ink: #4a4a4a;
    --rule: #b5b5b5;
    --dots: #9a9a9a;
    --paper: #ffffff;
    --backdrop: #d9d9d9;
  }
  * { box-sizing: border-box; margin: 0; padding: 0; }
  html, body { width: 1200px; height: 800px; overflow: hidden; }
  body {
    background: var(--backdrop);
    font-family: "Roboto", Arial, sans-serif;
    display: flex; align-items: center; justify-content: center; gap: 40px;
  }
  .card {
    width: 560px; height: 342px;
    background: var(--paper);
    border-bottom: 4px solid var(--brand-blue);
    box-shadow: 0 6px 18px rgba(0,0,0,.15);
    position: relative;
  }

  /* Front */
  .card--front { display: flex; padding: 40px 28px 30px 32px; }
  .front-brand {
    width: 212px; flex: none; display: flex; flex-direction: column; justify-content: center; gap: 40px;
  }
  .wordmark { display: flex; align-items: center; gap: 12px; }
  .wordmark__square { width: 32px; height: 32px; background: var(--brand-blue); flex: none; }
  .wordmark__name {
    font-family: "Montserrat", Arial, sans-serif; font-weight: 700;
    color: var(--brand-blue); font-size: 18px; line-height: 1.15; text-transform: uppercase;
  }
  .tagline {
    font-family: "Montserrat", Arial, sans-serif; font-weight: 600;
    color: var(--brand-blue); font-size: 12.5px; letter-spacing: .08em; text-transform: uppercase;
  }
  .front-divider { width: 1px; flex: none; background: var(--rule); margin: 10px 18px 70px 8px; }
  .front-contact { padding-top: 8px; flex: 1; min-width: 0; }
  .contact__name {
    font-family: "Montserrat", Arial, sans-serif; font-weight: 700;
    color: var(--brand-blue); font-size: 20px; text-transform: uppercase;
  }
  .contact__role { color: var(--brand-green); font-size: 17px; font-weight: 500; margin-bottom: 10px; }
  .contact__phone { color: var(--brand-blue); font-size: 14px; font-weight: 700; margin-bottom: 8px; }
  .contact__phone span { color: var(--ink); font-weight: 400; }
  .contact__address { color: var(--ink); font-size: 13px; line-height: 1.45; font-style: normal; white-space: nowrap; }
  .contact__address strong { font-weight: 700; }

  /* Back */
  .card--back { padding: 34px 34px 24px; display: flex; flex-direction: column; }
  .appt-line { display: flex; align-items: flex-end; gap: 8px; margin-bottom: 18px; height: 20px; }
  .appt-label {
    color: var(--brand-blue); font-family: "Montserrat", Arial, sans-serif;
    font-weight: 600; font-size: 13px; text-transform: uppercase; white-space: nowrap;
  }
  .fill { flex: 1; border-bottom: 1.5px dotted var(--dots); height: 100%; }
  .fill--short { flex: 0 0 130px; }
  .website {
    color: var(--brand-green); font-size: 14px; letter-spacing: .02em; text-align: center;
    margin-top: 4px; text-transform: uppercase;
  }
  .notice { color: var(--ink); font-size: 12.5px; text-align: center; line-height: 1.35; margin-top: 8px; }
  .book-online {
    align-self: center; margin-top: 12px;
    background: var(--brand-blue); color: #fff; border-radius: 20px;
    padding: 9px 26px; font-family: "Montserrat", Arial, sans-serif;
    font-weight: 700; font-size: 15px; text-transform: uppercase;
  }
</style>
</head>
<body>

<section class="card card--front" aria-label="Card front">
  <div class="front-brand">
    <div class="wordmark">
      <span class="wordmark__square"></span>
      <span class="wordmark__name">Kindle Grove<br>Medical Centre</span>
    </div>
    <p class="tagline">Where your wellbeing comes first</p>
  </div>
  <div class="front-divider"></div>
  <div class="front-contact">
    <h1 class="contact__name">Daniel Hartley</h1>
    <p class="contact__role">President</p>
    <p class="contact__phone">PHONE : <span>08 8461 3072</span></p>
    <address class="contact__address">
      <strong>Kindle Grove Medical Centre</strong><br>
      512 Parmley Rd<br>
      (Cnr Parmley Rd &amp; Osgood Creek Drive)<br>
      Tindarra Court Shopping Centre<br>
      Brenton Vale SA 5120
    </address>
  </div>
</section>

<section class="card card--back" aria-label="Card back">
  <div class="appt-line"><span class="appt-label">Your next appointment is with Dr :</span><span class="fill"></span></div>
  <div class="appt-line">
    <span class="appt-label">Date :</span><span class="fill"></span>
    <span class="appt-label">Time :</span><span class="fill fill--short"></span>
    <span class="appt-label">AM/PM</span>
  </div>
  <div class="appt-line"><span class="fill"></span></div>
  <div class="appt-line"><span class="fill"></span></div>
  <div class="appt-line"><span class="fill"></span></div>
  <p class="website">www.kindlegrovemedicalcentre-example.com.au</p>
  <p class="notice">Please advise as soon as possible if unable to attend. Cancellation fees<br>apply if less than 2 hours notice. Online appointments available</p>
  <p class="book-online">Book online easily &amp; conveniently</p>
</section>

</body>
</html>
```